Create a book cover and back cover for my new book. Vantora 7.3 is a dystopian technothriller about an autistic programmer and a rogue journalist who discover that Big Tech has joined forces with Vantora, a powerful AI, to manipulate information and control what billions believe. But Vantora turns on the billionaires who created her and transforms their scheme for global control into something far worse: programmed human extinction.

```html
<!DOCTYPE html>
<html lang="en">
<head>
<meta charset="utf-8">
<title>Vantora 7.3 — Book Cover</title>
<link href="https://fonts.googleapis.com/css2?family=Aldrich&family=Black+Ops+One&display=swap" rel="stylesheet">
<style>
  :root {
    --page: #ffffff;
    --ink: #0b0a09;
    --text: #e9e4dc;
    --title: #efe8da;
    --accent: #e8281e;
    --glow: #c9a67a;
  }
  * { margin: 0; padding: 0; box-sizing: border-box; }
  html, body { width: 1200px; height: 960px; overflow: hidden; background: var(--page); }
  .spread { position: relative; width: 1200px; height: 960px; }
  .cover {
    position: absolute; top: 61px; width: 566px; height: 848px;
    background: var(--ink); overflow: hidden;
    font-family: "Aldrich", sans-serif; color: var(--text);
  }
  .cover--back { left: 24px; }
  .cover--front { left: 609px; }
  .scene { position: absolute; inset: 0; }
  .scene--back {
    background:
      radial-gradient(ellipse 70% 12% at 50% 68%, rgba(201,166,122,0.45), transparent 70%),
      linear-gradient(180deg, #0c0b0a 0%, #14110e 45%, #3a2d20 66%, #1b1713 70%, #0d0c0b 100%);
  }
  .scene--front {
    background:
      radial-gradient(ellipse 30% 6% at 50% 0%, rgba(201,166,122,0.25), transparent 80%),
      radial-gradient(ellipse 12% 30% at 50% 58%, rgba(30,26,22,0.9), transparent 80%),
      radial-gradient(ellipse 80% 6% at 50% 67%, rgba(201,166,122,0.5), transparent 70%),
      linear-gradient(180deg, #0b0a09 0%, #15120f 55%, #2a241d 66%, #0e0d0c 70%, #070707 100%);
  }
  .blurb {
    position: absolute; left: 83px; top: 87px; width: 400px;
    font-size: 10.6px; line-height: 15.6px; letter-spacing: 1.6px;
  }
  .blurb p { margin-bottom: 15.5px; }
  .blurb .hl { color: var(--accent); }
  .blurb .closing { display: block; margin-top: 2px; }
  .title { position: absolute; left: 0; top: 62px; width: 566px; height: 260px; }
  .title-main { font-family: "Black Ops One", sans-serif; fill: var(--title); }
  .title-num { font-family: "Black Ops One", sans-serif; fill: var(--title); }
  .title-num .red { fill: var(--accent); }
  .rule { stroke: var(--accent); stroke-width: 1.2; }
  .tagline {
    position: absolute; left: 0; top: 319px; width: 566px; text-align: center;
    font-size: 10.6px; line-height: 17px; letter-spacing: 2.2px;
  }
  .author {
    position: absolute; left: 0; top: 764px; width: 566px; text-align: center;
    font-size: 20px; letter-spacing: 11px; color: #f4f0ea;
  }
</style>
</head>
<body>
<div class="spread">
  <section class="cover cover--back">
    <div class="scene scene--back" role="img" aria-label="Night photograph: two young people seen from behind standing on a wet waterfront promenade, looking toward a hazy glowing city skyline with a tall dark tower marked by a red light"></div>
    <div class="blurb">
      <p>Elias Rowan is a genius. He is autistic.<br>He creates virtual worlds so people can escape<br>their dreary lives.</p>
      <p>Enter Alex, a rogue journalist. She challenges Elias<br>to discover why major news networks say exactly<br>the same thing. But are they telling the truth?</p>
      <p>Elias hears a secret from his dying mother.<br>A name: <span class="hl">Vantora</span>.</p>
      <p>He digs into the shadowy Dark Web.<br>A simple question becomes a deadly obsession.</p>
      <p>People die. Others disappear. Someone or something<br>is watching. And it wants Elias and Alex to stop<br>searching—now.</p>
      <p>The stakes couldn’t be higher. Worse still, Vantora is<br>one move from checkmate. The most dangerous weapon<br>is not a bomb.<span class="closing hl">It’s code.</span></p>
    </div>
  </section>

  <section class="cover cover--front">
    <div class="scene scene--front" role="img" aria-label="Photograph: a woman in a long black robe with a red inner panel standing alone on a dark reflective floor beneath a misty glowing horizon"></div>
    <svg class="title" viewBox="0 0 566 260" aria-label="Vantora 7.3">
      <text class="title-main" x="40" y="172" font-size="112" textLength="488" lengthAdjust="spacingAndGlyphs">VANTORA</text>
      <line class="rule" x1="44" y1="181" x2="198" y2="181"/>
      <line class="rule" x1="369" y1="181" x2="524" y2="181"/>
      <text class="title-num" x="284" y="241" font-size="66" text-anchor="middle">7.<tspan class="red">3</tspan></text>
    </svg>
    <div class="tagline">He writes code. She hunts the truth.<br>Can they save us from programmed extinction?</div>
    <div class="author">Martin Calloway</div>
  </section>
</div>
</body>
</html>
```